Business card design for new eCommerce site focusing on integrity and strong businsess tactics

We need a business card that will stand out and be memorable. Something with color that matches our company logo colors. Think high end version of Pactivo. There are 2 logos provided. The parent company is called Amber Ledge Partners and we are presenting a new and very exciting eCommerce site called BrightHarborTrade.example.

Target Market(s)

Our target markets are in the Activities, Food and Beverage, Health and Beauty

Industry/Entity Type

Marketing

Contact Information for Business Card

We have 4 members that need cards...I will provide all info to the winner of the design contest
Business Address is
4870 West 63rd Avenue, Suite C207
Phoenix AZ 85731

Font styles to use
Serif
Sans Serif

Colors

Designer to choose colors to be used in the design.

Requirements
Must have
• The card must be memorable...should be unique in design but must exude integrity and be playful .
• I have provided several colors or our parent company...please feel free to use which ever
Nice to have
• I will leave this up to you. Feel free to use other images of your choosing that wraps around our client.....Activities, Dining, Health, Beauty
Should not have
• just dont be boring

```html
<!DOCTYPE html>
<html lang="en">
<head>
<meta charset="utf-8">
<title>BrightHarborTrade.example – Business Card</title>
<link rel="stylesheet" href="https://fonts.googleapis.com/css2?family=Didact+Gothic&family=Catamaran:wght@600;700&display=swap">
<style>
  :root {
    --backdrop: #2b2b2b;
    --paper: #f3f3f3;
    --brand-blue: #2b78a8;
    --brand-green: #6cb532;
    --ink: #4a4a4a;
    --white: #ffffff;
  }
  html, body {
    margin: 0;
    width: 1200px;
    height: 960px;
    overflow: hidden;
    background: var(--backdrop);
  }
  .stage { position: relative; width: 1200px; height: 960px; }
  .card {
    position: absolute;
    width: 600px;
    height: 342px;
    overflow: hidden;
    box-shadow: 0 2px 6px rgba(0,0,0,.45);
    font-family: "Didact Gothic", sans-serif;
  }
  .card-front { left: 314px; top: 113px; background: var(--paper); }
  .card-back { left: 311px; top: 472px; background: var(--brand-blue); }

  .brand { position: absolute; left: 36px; top: 56px; }
  .brand-name {
    margin: 0;
    font-family: "Catamaran", sans-serif;
    font-weight: 700;
    font-size: 28px;
    line-height: 1;
    color: var(--brand-green);
    display: flex;
    align-items: center;
    gap: 10px;
  }
  .brand-dot { width: 14px; height: 14px; border-radius: 50%; background: var(--brand-blue); }
  .brand-tagline {
    margin: 6px 0 0 24px;
    font-size: 13px;
    letter-spacing: 1px;
    color: var(--ink);
  }

  .contact-band {
    position: absolute;
    left: 0; top: 162px;
    width: 600px; height: 142px;
    background: var(--brand-blue);
  }
  .accent-panel { position: absolute; left: 0; top: 0; }
  .contact {
    position: absolute;
    left: 35px; top: 18px;
    color: var(--white);
    font-size: 14.5px;
    line-height: 19px;
  }
  .contact p { margin: 0; }
  .contact ul { list-style: none; margin: 8px 0 0; padding: 0; }
  .contact li { display: flex; align-items: center; gap: 8px; }
  .contact svg { width: 13px; height: 13px; fill: var(--white); }

  .person {
    position: absolute;
    right: 38px; top: 46px;
    text-align: right;
    color: var(--white);
  }
  .person-name {
    margin: 0;
    font-family: "Catamaran", sans-serif;
    font-weight: 600;
    font-size: 22px;
    line-height: 24px;
  }
  .person-role { margin: 0; font-size: 14.5px; }

  .website {
    position: absolute;
    left: 35px; bottom: 11px;
    margin: 0;
    font-size: 14.5px;
    color: var(--ink);
  }

  .back-mark {
    position: absolute;
    left: 228px; top: 70px;
    width: 142px; height: 142px;
    border: 3px solid var(--white);
    border-radius: 50%;
    box-sizing: border-box;
  }
  .back-name {
    position: absolute;
    left: 0; right: 0; top: 218px;
    margin: 0;
    text-align: center;
    font-family: "Catamaran", sans-serif;
    font-weight: 700;
    font-size: 36px;
    color: var(--white);
  }
</style>
</head>
<body>
<main class="stage">
  <section class="card card-front" aria-label="Card front">
    <div class="brand">
      <h1 class="brand-name"><span class="brand-dot"></span>BrightHarborTrade.example</h1>
      <p class="brand-tagline">Activities-Dining-Health-Beauty</p>
    </div>

    <div class="contact-band">
      <svg class="accent-panel" width="600" height="142" viewBox="0 0 600 142" aria-hidden="true">
        <polygon points="348,0 600,0 600,142 431,142" fill="var(--brand-green)"/>
      </svg>
      <address class="contact" style="font-style:normal">
        <p>4870 West 63rd Avenue</p>
        <p>Suite C207, Phoenix AZ 85731</p>
        <ul>
          <li><svg viewBox="0 0 24 24"><path d="M6.6 10.8a15 15 0 0 0 6.6 6.6l2.2-2.2c.3-.3.7-.4 1-.2 1.1.4 2.3.6 3.6.6.6 0 1 .4 1 1V20c0 .6-.4 1-1 1A17 17 0 0 1 3 4c0-.6.4-1 1-1h3.5c.6 0 1 .4 1 1 0 1.3.2 2.5.6 3.6.1.3 0 .7-.2 1z"/></svg>602 555 0148</li>
          <li><svg viewBox="0 0 24 24"><path d="M7 1h10a2 2 0 0 1 2 2v18a2 2 0 0 1-2 2H7a2 2 0 0 1-2-2V3a2 2 0 0 1 2-2zm0 3v14h10V4zm5 15.5a1 1 0 1 0 0 2 1 1 0 0 0 0-2z"/></svg>602 555 0193</li>
          <li><svg viewBox="0 0 24 24"><path d="M2 5h20v14H2zm2 2v.5l8 5 8-5V7z"/></svg>dana@brightharbortrade.example</li>
        </ul>
      </address>
      <div class="person">
        <p class="person-name">DANA WHITFIELD</p>
        <p class="person-role">CEO/FOUNDER</p>
      </div>
    </div>

    <p class="website">www.brightharbortrade.example</p>
  </section>

  <section class="card card-back" aria-label="Card back">
    <div class="back-mark" aria-hidden="true"></div>
    <h2 class="back-name">Amber Ledge Partners</h2>
  </section>
</main>
</body>
</html>
```